A5, portrait
Theme is science
audience is VIPS, politicians, executives
this is a really important event, we want a very classy invitation
include logo for bloom and grow and lantern but lantern one bigger
images attached
Have attached some styles we like but doesn't need to be these colours. If we can incorporate some colours from our logo would be good but don't make too colourful and childish

You’re invited to the official opening and launch of Lantern, Centre of Discovery. an industry first, pioneering, STEM hub.

Saturday 30th April, 2022

10:00 am – 12:00 pm

42 Harlow Lane, Fernwood

Light canapes provided. Dress code is smart/casual

All guests will be given a guided walk through of Australia’s first dedicated STEM education hub for children aged 3-6.

Invitation only

RSVP: 18 April to marketing@bloomandgrow.edu.au

```html
<!DOCTYPE html>
<html lang="en">
<head>
<meta charset="utf-8">
<title>Lantern, Centre of Discovery – Official Opening Invitation</title>
<link rel="stylesheet" href="https://fonts.googleapis.com/css2?family=Tinos:wght@400;700&display=swap">
<style>
  :root {
    --page: #e9e6e0;
    --navy-deep: #15132a;
    --navy: #2a2651;
    --navy-mid: #302b5c;
    --ink-light: #f4f3fb;
    --ink-dark: #2b2a45;
    --photo-a: #2f35a6;
    --photo-b: #6d62d6;
    --photo-c: #1d1f6e;
    --accent: #f2c230;
    --paper: #ffffff;
  }
  * { box-sizing: border-box; margin: 0; padding: 0; }
  html, body {
    width: 1200px; height: 900px; overflow: hidden;
    background: var(--page);
  }
  .invitation {
    position: absolute; left: 297px; top: 20px;
    width: 606px; height: 860px;
    background: linear-gradient(150deg, var(--navy-deep) 0%, var(--navy) 35%, var(--navy-mid) 60%, var(--navy) 85%, var(--navy-deep) 100%);
    font-family: "Tinos", "Times New Roman", serif;
    color: var(--ink-light);
    text-align: center;
    box-shadow: 0 6px 18px rgba(0,0,0,0.25);
  }
  .brand {
    position: absolute; top: 62px; left: 0; right: 0;
  }
  .brand-name {
    display: inline-flex; align-items: center; gap: 10px;
    font-size: 40px; font-weight: 700; letter-spacing: 4px;
    color: var(--ink-light); text-transform: uppercase;
  }
  .brand-name .dot {
    width: 22px; height: 22px; border-radius: 50%;
    background: var(--accent);
  }
  .brand-tagline {
    margin-top: 6px; font-size: 15px; font-weight: 700; letter-spacing: 1px;
    color: var(--ink-light);
  }
  .welcome {
    position: absolute; top: 192px; left: 0; right: 0;
    font-size: 22px; line-height: 32px;
  }
  .details {
    position: absolute; top: 346px; left: 0; right: 0;
    font-size: 22px; line-height: 32px;
  }
  .venue-photo {
    position: absolute; top: 462px; left: 0;
    width: 606px; height: 195px;
    background:
      radial-gradient(ellipse 70px 70px at 50% 52%, #8f86e8 0%, rgba(143,134,232,0) 100%),
      linear-gradient(90deg, var(--photo-c) 0%, var(--photo-a) 30%, var(--photo-b) 55%, var(--photo-a) 80%, var(--photo-c) 100%);
  }
  .notes {
    position: absolute; top: 683px; left: 0; right: 0;
    font-size: 14px; line-height: 17px;
  }
  .notes p + p { margin-top: 0; }
  .notes .walk { line-height: 22px; }
  .access {
    position: absolute; top: 761px; left: 227px;
    width: 151px; height: 26px;
    border: 2px solid var(--ink-light);
    font-size: 15px; line-height: 22px; letter-spacing: 0.3px;
  }
  .partner {
    position: absolute; top: 752px; left: 470px; width: 126px;
    display: flex; align-items: center; justify-content: flex-end; gap: 6px;
    font-size: 13px; font-weight: 700; color: var(--ink-light);
  }
  .partner .tile {
    width: 12px; height: 12px; background: var(--accent);
  }
  .rsvp {
    position: absolute; bottom: 0; left: 0;
    width: 606px; height: 40px;
    background: var(--paper); color: var(--ink-dark);
    font-size: 19px; line-height: 40px;
  }
</style>
</head>
<body>
  <article class="invitation">
    <header class="brand">
      <div class="brand-name"><span class="dot"></span>Lantern</div>
      <div class="brand-tagline">Centre of Discovery</div>
    </header>

    <p class="welcome">
      You’re invited to the official opening and<br>
      launch of Lantern, Centre of Discovery.<br>
      An industry first, pioneering, STEM hub.
    </p>

    <p class="details">
      Saturday 30th April, 2022<br>
      10:00 am – 12:00 pm<br>
      42 Harlow Lane, Fernwood
    </p>

    <div class="venue-photo" role="img" aria-label="Photo of a glowing plasma ball on a plinth inside the blue-lit STEM centre"></div>

    <section class="notes">
      <p>Light canapes provided. Dress code is smart/casual</p>
      <p class="walk">All guests will be given a guided walk through of Australia’s first<br>
      dedicated STEM education hub for children aged 3-6.</p>
    </section>

    <div class="access">INVITATION ONLY</div>

    <div class="partner"><span class="tile"></span>Bloom &amp; Grow</div>

    <footer class="rsvp">RSVP: 18 April to marketing@bloomandgrow.edu.au</footer>
  </article>
</body>
</html>
```